Talvane Aerial webdesign: Innovative Drones service company in agriculture

We need a new website according the following conditions:
• Main colour orange and current logo;
• Transparent – open – trustworthy – dynamic - personal;
• Use the smartness and overview characteristics of the crow (Talvane is Latin for crow);
• Accessible to multiple target groups and markets:
o So not too horticultural, too green;
• Use contradictions:
o Future versus nostalgia;
o Smartness crow versus precision hummingbird;
o Technology versus mechanical;
• Kestrand 2.4 LTX as a style icon?
• Long pager website
Updates

Website menu o Home o Crop monitoring  Applications Growth | Stress | Development | Diseases  Markets Breeding | Young plant | Potplants | Cutflowers | Vegetables | Soft fruit  Customer cases o Technology Aerial data collection | Artificial intelligence | Free data sets o About Vision | Company | Partners | Team | Career o Contact o News&downloads Logo: www.talvaneaerial-example.com

Target Market(s)

agriculture: owners, crop managers
oil&gas: maintenance, quality control managers and purchase managers
logistics: ware house managers, purchase managers

Industry/Entity Type

Agribusiness

Number of Pages Required

2 page

Colors
f78f20

Requirements
Must have
• long pager website
downloads
Linkwork
Should not have
• Not too 'green' because first impression of designers of agriculture/horticulture is using the green colour. But that is not necessary.

Keep in mind that the current logo will be updates: the circle will be more 'general' and less 'agri'. Also the green colors in the logo will be slightly darker to make it more powerful.

```html
<!DOCTYPE html>
<html lang="en">
<head>
<meta charset="utf-8">
<title>Talvane Aerial</title>
<link rel="stylesheet" href="https://fonts.googleapis.com/css2?family=Montserrat:wght@400;500;600;700&display=swap">
<style>
:root{
  --orange:#f07722;
  --orange-soft:#f39a4f;
  --green:#8db133;
  --dark:#1f1f1f;
  --text:#555;
  --grey-bg:#f1f1f1;
  --grey-mid:#a9a9a9;
  --line:#f3b07a;
  --white:#fff;
}
*{box-sizing:border-box;margin:0;padding:0}
html,body{width:1200px;height:4199px;overflow:hidden}
body{position:relative;font-family:"Montserrat",sans-serif;color:var(--text);background:var(--white)}
.shapes{position:absolute;left:0;top:0}
/* header */
.site-header{position:absolute;left:0;top:0;width:1200px;height:98px;background:rgba(40,40,40,.55);z-index:3}
.brand{position:absolute;left:76px;top:18px;display:flex;align-items:center;gap:14px}
.brand-dot{width:58px;height:58px;border-radius:50%;background:var(--white)}
.brand-name{color:var(--white);font-weight:600;font-size:34px;letter-spacing:1px;line-height:1}
.main-nav{position:absolute;right:74px;top:36px;display:flex;gap:36px}
.main-nav a{color:#eee;font-size:13px;text-decoration:none;letter-spacing:.3px}
.main-nav a.active{color:var(--white);font-weight:700;position:relative}
.main-nav a.active::after{content:"";position:absolute;left:8px;right:8px;top:22px;height:3px;background:var(--orange)}
/* hero */
.hero-photo{position:absolute;left:0;top:0}
.hero-badge{position:absolute;left:668px;top:180px;width:408px;height:408px;border-radius:50%;background:rgba(240,119,34,.94);text-align:center;color:var(--white);z-index:2}
.hero-badge .mark{width:56px;height:56px;border-radius:50%;background:var(--white);margin:74px auto 14px}
.hero-badge h1{font-size:30px;font-weight:500;line-height:36px;letter-spacing:.5px}
.hero-badge h1 b{font-weight:700}
.btn-outline-white{display:inline-block;margin-top:24px;border:2px solid var(--white);border-radius:26px;color:var(--white);font-size:14px;font-weight:700;padding:13px 34px}
.arrow{position:absolute;top:375px;z-index:2}
/* section headings */
.sec-title{position:absolute;left:0;width:1200px;text-align:center;font-size:30px;font-weight:700;color:var(--dark);letter-spacing:.3px}
.sec-title::after{content:"";display:block;width:74px;height:3px;background:var(--green);margin:8px auto 0}
.sec-title.light{color:var(--white)}
.sec-title.light::after{background:var(--white)}
/* cards */
.service-card{position:absolute;top:898px;width:330px;height:240px;border:2px solid var(--line);text-align:center}
.service-card .icon{position:absolute;left:109px;top:-58px;width:112px;height:112px;border-radius:50%;background:var(--orange)}
.service-card h3{margin-top:70px;font-size:19px;font-weight:700;color:var(--dark)}
.service-card p{margin:12px auto 0;width:290px;font-size:13.5px;line-height:23px}
.btn-outline-green{display:inline-block;margin-top:14px;border:2px solid var(--green);border-radius:24px;color:var(--green);font-size:13px;font-weight:700;padding:11px 32px}
/* about */
.about-art{position:absolute;left:98px;top:1280px;width:424px;height:383px;border-radius:10px;background:radial-gradient(ellipse at center,#cfcfcf,#f1f1f1 70%)}
.about-text{position:absolute;left:588px;top:1322px;width:520px}
.about-text h2{font-size:32px;font-weight:700;color:var(--orange)}
.about-text p{margin-top:26px;font-size:15px;line-height:26.6px;color:#555}
.btn-green{display:inline-block;background:var(--green);color:var(--white);border-radius:24px;font-size:14px;font-weight:700}
.about-text .btn-green{margin-top:24px;padding:14px 36px}
/* feature circles */
.feature{position:absolute;top:1850px;width:374px;height:374px;border-radius:50%;text-align:center;color:var(--white);overflow:hidden}
.feature.photo{background:radial-gradient(circle at 50% 40%,#6b5f55,#3a3430 55%,#2a2623)}
.feature.ai{background:radial-gradient(circle,#90bb35,#7ea72b);box-shadow:0 20px 40px rgba(0,0,0,.25);z-index:2}
.feature svg{margin-top:78px}
.feature h3{margin-top:14px;font-size:21px;font-weight:700;line-height:28px;letter-spacing:.3px}
.feature p{margin:10px auto 0;width:260px;font-size:13px;line-height:22px;color:#eee}
/* partners */
.partner{position:absolute;background:#b9b9b9}
/* news */
.news-card{position:absolute;top:2866px;width:294px;height:384px;background:var(--white);box-shadow:0 4px 14px rgba(0,0,0,.08)}
.news-card .thumb{height:171px}
.news-card .body{padding:22px 30px 0}
.news-card time{display:block;font-size:12.5px;font-weight:600;color:var(--green)}
.news-card h3{margin-top:12px;font-size:17px;font-weight:500;line-height:20px;color:var(--dark)}
.news-card p{margin-top:10px;font-size:11.5px;line-height:19px;color:#777}
.news-card .more{display:block;margin-top:12px;font-size:12px;font-weight:700;color:var(--orange)}
/* contact */
.contact-title{position:absolute;left:132px;top:3422px;font-size:30px;font-weight:700;color:var(--dark)}
.contact-title::after{content:"";display:block;width:56px;height:3px;background:var(--green);margin-top:8px}
.field{position:absolute;border:1px solid #9a9a9a;background:var(--white);font-size:15px;color:#333;padding:12px 18px}
.submit{position:absolute;left:124px;top:3723px;width:171px;height:45px;line-height:45px;text-align:center;font-size:17px;border-radius:24px}
.car-art{position:absolute;left:628px;top:3482px;width:532px;height:316px;border-radius:12px;background:radial-gradient(ellipse at 50% 55%,#f07722 0%,#e8743a 35%,#d9d9d9 70%,#fff 100%)}
/* footer */
.site-footer{position:absolute;left:0;top:3855px;width:1200px;height:344px;background:var(--orange);color:var(--white)}
.foot-col{position:absolute;top:70px}
.foot-col h4{font-size:19px;font-weight:700;letter-spacing:.2px}
.foot-col ul{list-style:none;margin-top:14px}
.foot-col li{font-size:14.5px;line-height:28.5px;color:#fde3cf}
.foot-contact li{display:flex;align-items:center;gap:10px}
.socials{display:flex;gap:18px;margin-top:16px;margin-left:4px}
.socials span{display:flex;align-items:center;gap:6px;font-size:13px;font-weight:600}
.socials span::before{content:"";width:10px;height:10px;border-radius:50%;background:var(--white)}
.foot-rule{position:absolute;left:132px;right:132px;top:270px;height:1px;background:rgba(255,255,255,.35)}
.copyright{position:absolute;left:0;width:1200px;top:290px;text-align:center;font-size:14px;color:#fde3cf}
</style>
</head>
<body>

<svg class="shapes" width="1200" height="4199" viewBox="0 0 1200 4199" aria-hidden="true">
  <polygon points="0,1182 1200,1235 1200,1690 0,1672" fill="#f1f1f1"/>
  <polygon points="774,1248 1200,1197 1200,1280" fill="#8db133"/>
  <polygon points="0,1672 700,1690 0,1780" fill="#a9a9a9"/>
  <polygon points="0,1780 1200,1645 1200,2192 0,2274" fill="#f07722"/>
  <polygon points="0,2698 1200,2725 1200,3350 0,3350" fill="#f1f1f1"/>
  <polygon points="766,2755 1200,2690 1200,2787" fill="#f07722"/>
</svg>

<svg class="hero-photo" width="1200" height="720" viewBox="0 0 1200 720" role="img" aria-label="Drone flying over rows of flowering plants inside a greenhouse">
  <defs>
    <linearGradient id="heroGrad" x1="0" y1="0" x2="0" y2="1">
      <stop offset="0" stop-color="#8e9a93"/>
      <stop offset=".35" stop-color="#4f7a3a"/>
      <stop offset="1" stop-color="#3d6b2a"/>
    </linearGradient>
  </defs>
  <polygon points="0,0 1200,0 1200,630 600,700 0,640" fill="url(#heroGrad)"/>
</svg>

<header class="site-header">
  <div class="brand"><span class="brand-dot"></span><span class="brand-name">TALVANE</span></div>
  <nav class="main-nav">
    <a class="active">HOME</a><a>CROP MONITORING</a><a>TECHNOLOGY</a><a>ABOUT</a><a>CONTACT</a><a>NEWS &amp; DOWNLOADS</a>
  </nav>
</header>

<svg class="arrow" style="left:40px" width="30" height="44" viewBox="0 0 30 44" aria-hidden="true"><polyline points="24,4 6,22 24,40" fill="none" stroke="#fff" stroke-width="5"/></svg>
<svg class="arrow" style="left:1152px" width="30" height="44" viewBox="0 0 30 44" aria-hidden="true"><polyline points="6,4 24,22 6,40" fill="none" stroke="#fff" stroke-width="5"/></svg>

<section class="hero-badge">
  <div class="mark"></div>
  <h1>ENABLES AERIAL<br><b>DATA-COLLECTION IN<br>GREENHOUSES</b></h1>
  <span class="btn-outline-white">LEARN MORE</span>
</section>

<h2 class="sec-title" style="top:772px">CROP MONITORING</h2>

<article class="service-card" style="left:82px">
  <div class="icon"><svg width="112" height="112" viewBox="0 0 112 112" aria-hidden="true"><g fill="none" stroke="#fff" stroke-width="3"><rect x="32" y="32" width="48" height="36" rx="2"/><rect x="40" y="40" width="22" height="14"/><line x1="48" y1="76" x2="64" y2="76"/><line x1="56" y1="68" x2="56" y2="76"/></g></svg></div>
  <h3>APPLICATIONS</h3>
  <p>Augiat in pede Fusce tellus Sed metus augue convallis et vehicula ut pulvinar</p>
  <span class="btn-outline-green">LEARN MORE</span>
</article>
<article class="service-card" style="left:429px">
  <div class="icon"><svg width="112" height="112" viewBox="0 0 112 112" aria-hidden="true"><g fill="none" stroke="#fff" stroke-width="3"><path d="M28 72 V52 Q28 34 50 32 H62 Q84 34 84 52 V72 Z"/><line x1="44" y1="34" x2="44" y2="72"/><line x1="56" y1="32" x2="56" y2="72"/><line x1="68" y1="34" x2="68" y2="72"/></g></svg></div>
  <h3>MARKETS</h3>
  <p>Augiat in pede Fusce tellus Sed metus augue convallis et vehicula ut pulvinar</p>
  <span class="btn-outline-green">LEARN MORE</span>
</article>
<article class="service-card" style="left:782px">
  <div class="icon"><svg width="112" height="112" viewBox="0 0 112 112" aria-hidden="true"><g fill="none" stroke="#fff" stroke-width="3"><circle cx="56" cy="44" r="8"/><circle cx="38" cy="48" r="6"/><circle cx="74" cy="48" r="6"/><path d="M42 74 V66 Q42 56 56 56 Q70 56 70 66 V74 Z"/><path d="M28 72 V66 Q28 58 38 58"/><path d="M84 72 V66 Q84 58 74 58"/></g></svg></div>
  <h3>CUSTOMER CASES</h3>
  <p>Augiat in pede Fusce tellus Sed metus augue convallis et vehicula ut pulvinar</p>
  <span class="btn-outline-green">LEARN MORE</span>
</article>

<div class="about-art" role="img" aria-label="Ink drawing of a crow in flight with wings spread"></div>
<section class="about-text">
  <h2>ABOUT TALVANE AERIAL</h2>
  <p>Talvane Aerial has developed a unique autonomous drone system that is able to fly and navigate in a greenhouse without manual interference. Based on a flight plan the drone follows the right coordinates in the greenhouse, day or night, collecting high accurate data.<br>Data is being interpreted by Artificial Intelligence software resulting in crop improvement information.</p>
  <span class="btn-green">LEARN MORE</span>
</section>

<h2 class="sec-title light" style="top:1765px">CROP MONITORING</h2>

<article class="feature photo" style="left:108px" role="img" aria-label="Drone in a greenhouse, dark photo background">
  <svg width="100" height="70" viewBox="0 0 100 70" aria-hidden="true"><g fill="none" stroke="#fff" stroke-width="3"><line x1="10" y1="10" x2="34" y2="10"/><line x1="66" y1="10" x2="90" y2="10"/><line x1="22" y1="10" x2="22" y2="28"/><line x1="78" y1="10" x2="78" y2="28"/><path d="M22 28 H78"/><rect x="38" y="28" width="24" height="20" rx="4"/><circle cx="50" cy="56" r="7"/></g></svg>
  <h3>AERIAL DATA<br>COLLECTION</h3>
  <p>Data is being interpreted by Artificial Intelligence software resulting</p>
</article>
<article class="feature ai" style="left:433px" role="img" aria-label="Green circuit board texture">
  <svg width="100" height="70" viewBox="0 0 100 70" aria-hidden="true"><g fill="none" stroke="#fff" stroke-width="3"><path d="M30 40 Q18 40 18 30 Q18 20 30 20 Q34 6 50 6 Q66 6 70 20 Q82 20 82 30 Q82 40 70 40 Z"/><rect x="40" y="18" width="20" height="18"/><line x1="50" y1="40" x2="50" y2="66"/><line x1="42" y1="40" x2="42" y2="58"/><line x1="58" y1="40" x2="58" y2="58"/></g></svg>
  <h3>ARTIFICIAL<br>INTELLIGENCE</h3>
  <p>Data is being interpreted by Artificial Intelligence software resulting</p>
</article>
<article class="feature photo" style="left:759px" role="img" aria-label="Drone above flowering greenhouse plants, dark photo background">
  <svg width="100" height="70" viewBox="0 0 100 70" aria-hidden="true"><g fill="none" stroke="#fff" stroke-width="3"><path d="M14 30 L50 6 L86 30"/><path d="M22 26 V66 H78 V26"/><path d="M40 66 V46 Q40 36 50 36 Q60 36 60 46 V66"/></g></svg>
  <h3>FREE DATA<br>SETS</h3>
  <p>Data is being interpreted by Artificial Intelligence software resulting</p>
</article>

<h2 class="sec-title" style="top:2316px">OUR PARTNERS</h2>
<div class="partner" style="left:110px;top:2424px;width:112px;height:38px;border-radius:19px"></div>
<div class="partner" style="left:336px;top:2432px;width:100px;height:28px"></div>
<div class="partner" style="left:534px;top:2430px;width:142px;height:30px;border-radius:4px"></div>
<div class="partner" style="left:764px;top:2433px;width:24px;height:24px"></div>
<div class="partner" style="left:800px;top:2439px;width:88px;height:12px;border-radius:3px"></div>
<div class="partner" style="left:978px;top:2428px;width:134px;height:36px;border-radius:18px"></div>
<div class="partner" style="left:128px;top:2534px;width:76px;height:76px;border-radius:50%"></div>
<div class="partner" style="left:336px;top:2540px;width:100px;height:62px"></div>
<div class="partner" style="left:546px;top:2552px;width:120px;height:34px;border-radius:4px"></div>
<div class="partner" style="left:762px;top:2545px;width:124px;height:48px;border-radius:4px"></div>
<div class="partner" style="left:988px;top:2552px;width:114px;height:40px;border-radius:4px"></div>

<h2 class="sec-title" style="top:2784px">LATEST NEWS</h2>

<article class="news-card" style="left:126px">
  <div class="thumb" role="img" aria-label="Red flowers growing under a greenhouse roof" style="background:linear-gradient(#4c86c6,#8fb4d8 45%,#e4572a 75%,#3d7a30)"></div>
  <div class="body"><time>JAN 20, 2020</time><h3>Curabitur iaculis tempus eros Curabitur vel</h3><p>Curabitur vel dolor ultrices ipsum dictum tristique Praesent vitae lacus Ut velit enim vestibulum non fermentum</p><span class="more">LEARN MORE ›</span></div>
</article>
<article class="news-card" style="left:458px">
  <div class="thumb" role="img" aria-label="Orange drone hovering above young plants in a greenhouse" style="background:linear-gradient(#b9c4be,#6f8c6a 55%,#2f5e2c)"></div>
  <div class="body"><time>JAN 15, 2020</time><h3>Nunc tempus felis vitae urna Vivamus</h3><p>Curabitur vel dolor ultrices ipsum dictum tristique Praesent vitae lacus Ut velit enim vestibulum non fermentum</p><span class="more">LEARN MORE ›</span></div>
</article>
<article class="news-card" style="left:791px">
  <div class="thumb" role="img" aria-label="Drone carrying a box over hydroponic plant rows" style="background:linear-gradient(#e8ece6,#b6d08a 55%,#5c8a2e)"></div>
  <div class="body"><time>JAN 10, 2020</time><h3>Praesent sit amet est In dictum dolor eu dictu</h3><p>Curabitur vel dolor ultrices ipsum dictum tristique Praesent vitae lacus Ut velit enim vestibulum non fermentum</p><span class="more">LEARN MORE ›</span></div>
</article>

<h2 class="contact-title">CONTACT US</h2>
<div class="field" style="left:132px;top:3497px;width:232px;height:45px">First Name</div>
<div class="field" style="left:373px;top:3497px;width:232px;height:45px">Last Name</div>
<div class="field" style="left:132px;top:3552px;width:232px;height:45px">Email address</div>
<div class="field" style="left:373px;top:3552px;width:232px;height:45px">Phone</div>
<div class="field" style="left:132px;top:3607px;width:475px;height:93px">Message</div>
<span class="btn-green submit">SUBMIT</span>
<div class="car-art" role="img" aria-label="Orange Kestrand 2.4 LTX classic coupe, front three-quarter view"></div>

<footer class="site-footer">
  <div class="foot-col" style="left:132px"><h4>COMPANY</h4><ul><li>Home</li><li>Technology</li><li>About</li><li>Vision</li></ul></div>
  <div class="foot-col" style="left:302px"><h4>CROP MONITORING</h4><ul><li>Applications</li><li>Markets</li><li>Customer cases</li></ul></div>
  <div class="foot-col" style="left:566px"><h4>RESOURCES</h4><ul><li>News</li><li>Downloads</li><li>Contact Us</li></ul></div>
  <div class="foot-col foot-contact" style="left:760px"><h4>CONTACT US</h4>
    <ul>
      <li><svg width="14" height="18" viewBox="0 0 14 18" aria-hidden="true"><path d="M7 1 C3 1 1 4 1 7 C1 11 7 17 7 17 C7 17 13 11 13 7 C13 4 11 1 7 1 Z" fill="#fff"/><circle cx="7" cy="7" r="2.5" fill="#f07722"/></svg>Veldhoflaan 14B, 4101AB, Ardenveld</li>
      <li><svg width="14" height="16" viewBox="0 0 14 16" aria-hidden="true"><path d="M3 1 L6 4 L4.5 6.5 Q6 10 9 11.5 L11.5 10 L14 13 L11 15 Q3 13 1 4 Z" fill="#fff"/></svg>Email: info@talvaneaerial-example.com</li>
      <li><svg width="14" height="14" viewBox="0 0 14 14" aria-hidden="true"><rect x="0" y="2" width="14" height="10" fill="#fff"/><polyline points="0,2 7,8 14,2" fill="none" stroke="#f07722" stroke-width="1.5"/></svg>Telephone: +31 6 00112233</li>
    </ul>
    <div class="socials"><span>Chirp</span><span>Facet</span><span>Linkwork</span></div>
  </div>
  <div class="foot-rule"></div>
  <p class="copyright">© 2020 Company Name | All Rights Reserved</p>
</footer>

</body>
</html>
```